business card design for a plumbing contractor

i need a double business card for a plumbing business, our initial service is residential Sewer Drain Cleaning.

Target Market(s)

other plumbing Business

Industry/Entity Type

Plumbing

Contact Information for Business Card

www.PipeworksTopMark.example- 5307218394-

Font styles to use
Serif

Colors
ec1f27
0455a3

```html
<!DOCTYPE html>
<html lang="en">
<head>
<meta charset="utf-8">
<title>Pipeworks Top Mark – Business Card</title>
<link rel="stylesheet" href="https://fonts.googleapis.com/css2?family=Open+Sans:wght@400;600;700;800&display=swap">
<style>
  :root {
    --backdrop: #2a2a2a;
    --brand-blue: #0455a3;
    --front-blue: #2f6aa6;
    --deep-blue: #12407a;
    --brand-red: #ec1f27;
    --ink-warm: #6b625a;
    --paper: #f6f6f6;
    --white: #ffffff;
  }
  * { box-sizing: border-box; margin: 0; padding: 0; }
  html, body {
    width: 1200px; height: 997px; overflow: hidden;
    background: var(--backdrop);
    font-family: "Open Sans", Arial, sans-serif;
  }
  .sheet {
    width: 1200px; height: 997px;
    display: flex; flex-direction: column; align-items: center; justify-content: center;
    gap: 57px;
  }
  .card {
    position: relative;
    width: 700px; height: 400px;
    border-radius: 22px;
    overflow: hidden;
  }

  /* Front */
  .card-front { background: var(--front-blue); }
  .card-front .brand {
    position: absolute; left: 0; right: 0; top: 118px;
    display: flex; align-items: center; justify-content: center; gap: 16px;
  }
  .brand-name {
    font-weight: 800; font-size: 50px; line-height: 1; letter-spacing: -0.5px;
  }
  .card-front .brand-name { color: var(--white); }
  .brand-dot {
    width: 26px; height: 26px; border-radius: 50%;
  }
  .card-front .brand-dot { background: var(--white); }
  .tagline-band {
    position: absolute; left: 0; right: 0; top: 298px; height: 34px;
    background: var(--brand-red);
    border-top: 2px solid #ff5a5f; border-bottom: 2px solid #b3141a;
    display: flex; align-items: center; justify-content: center;
    color: var(--white); font-size: 15px; font-weight: 600; letter-spacing: 1.2px;
    text-transform: uppercase;
  }

  /* Back */
  .card-back { background: var(--paper); }
  .card-back .shapes { position: absolute; inset: 0; }
  .card-back .brand {
    position: absolute; left: 0; right: 0; top: 70px;
    display: flex; align-items: center; justify-content: center; gap: 14px;
  }
  .card-back .brand-name { color: var(--ink-warm); font-size: 46px; }
  .card-back .brand-dot { background: var(--brand-red); width: 24px; height: 24px; }
  .holder {
    position: absolute; left: 220px; width: 360px; top: 206px;
    text-align: center; color: var(--white);
  }
  .holder-name { font-size: 27px; font-weight: 700; letter-spacing: 0.5px; line-height: 1.1; text-transform: uppercase; }
  .holder-role { font-size: 15px; font-weight: 600; }
  .website {
    position: absolute; right: 34px; top: 262px;
    color: var(--white); font-size: 17px; font-weight: 700;
  }
  .contacts {
    position: absolute; left: 34px; bottom: 30px;
    list-style: none; display: flex; flex-direction: column; gap: 12px;
    color: #e8eef7; font-size: 18px;
  }
  .contacts li { display: flex; align-items: center; gap: 12px; }
  .contact-icon {
    width: 22px; height: 22px; border-radius: 50%;
    background: var(--brand-red);
    display: flex; align-items: center; justify-content: center;
  }
</style>
</head>
<body>
<main class="sheet">

  <section class="card card-front" aria-label="Card front">
    <div class="brand">
      <span class="brand-name">Pipeworks Top Mark</span>
      <span class="brand-dot"></span>
    </div>
    <div class="tagline-band">Sewer drain cleaning, maintenance, trenchless pipe installs</div>
  </section>

  <section class="card card-back" aria-label="Card back">
    <svg class="shapes" width="700" height="400" viewBox="0 0 700 400" aria-hidden="true">
      <polygon points="0,244 180,244 214,192 586,192 620,168 700,168 700,176 624,176 590,200 218,200 184,252 0,252" fill="var(--brand-red)"/>
      <polygon points="0,252 184,252 218,200 590,200 624,176 700,176 700,400 0,400" fill="var(--brand-blue)"/>
      <polygon points="0,252 184,252 218,200 590,200 624,176 700,176 700,400 0,400" fill="var(--deep-blue)" opacity="0.35"/>
      <polygon points="196,262 226,198 574,198 604,262" fill="var(--brand-red)"/>
      <polygon points="196,262 226,198 232,198 204,262" fill="#b3141a"/>
    </svg>

    <div class="brand">
      <span class="brand-name">Pipeworks Top Mark</span>
      <span class="brand-dot"></span>
    </div>

    <div class="holder">
      <p class="holder-name">Dana Mercer</p>
      <p class="holder-role">Personal Trainer</p>
    </div>

    <p class="website">www.PipeworksTopMark.example</p>

    <ul class="contacts">
      <li>
        <span class="contact-icon">
          <svg width="12" height="12" viewBox="0 0 24 24" aria-hidden="true"><path fill="#fff" d="M6.6 10.8a15.1 15.1 0 0 0 6.6 6.6l2.2-2.2a1 1 0 0 1 1-.25 11.4 11.4 0 0 0 3.6.57 1 1 0 0 1 1 1V20a1 1 0 0 1-1 1A17 17 0 0 1 3 4a1 1 0 0 1 1-1h3.5a1 1 0 0 1 1 1c0 1.25.2 2.45.57 3.57a1 1 0 0 1-.25 1z"/></svg>
        </span>
        5307218394
      </li>
      <li>
        <span class="contact-icon">
          <svg width="12" height="12" viewBox="0 0 24 24" aria-hidden="true"><rect x="2" y="5" width="20" height="14" rx="2" fill="#fff"/><path d="M3 6l9 7 9-7" fill="none" stroke="#ec1f27" stroke-width="2"/></svg>
        </span>
        Dispatcher@PipeworksTopMark.example
      </li>
    </ul>
  </section>

</main>
</body>
</html>
```